Bramble Hockey Academy

We are are Ice Hockey Development Company that provided on-ice Hockey development services. We need a Landing Page with tabs to direct to individual program pages.
Landing Page
About Page
Winter Program Page
Spring Program Page
Summer Program Page
Team Page
Tournament Page

Coded - Design and coding required

5+ page

```html
<!DOCTYPE html>
<html lang="en">
<head>
<meta charset="utf-8">
<title>Bramble Hockey Academy</title>
<link href="https://fonts.googleapis.com/css2?family=Josefin+Sans:wght@600;700&family=Roboto:wght@400;500;700&display=swap" rel="stylesheet">
<style>
:root{
  --green:#127a12;
  --green-dark:#0b6a0b;
  --green-bright:#1f8f1f;
  --field:#3a9a3a;
  --ink:#222;
  --body:#666;
  --footer:#121212;
  --white:#fff;
}
*{box-sizing:border-box;margin:0;padding:0}
html,body{width:1200px;height:3600px;overflow:hidden}
body{position:relative;background:var(--white);font-family:'Roboto',sans-serif;color:var(--ink)}
.abs{position:absolute}
.heading{font-family:'Josefin Sans',sans-serif;font-weight:700;color:var(--ink);text-transform:uppercase}
.btn{position:absolute;display:flex;align-items:center;justify-content:center;background:var(--green);color:var(--white);font-weight:700;font-size:14px;text-transform:uppercase;letter-spacing:.2px}

/* header */
.site-header{position:absolute;left:0;top:0;width:1200px;height:97px;background:var(--white);border-bottom:1px solid #eee}
.brand{position:absolute;left:112px;top:30px;font-family:'Josefin Sans',sans-serif;font-weight:700;font-size:30px;color:var(--ink)}
.nav{position:absolute;top:45px;display:flex;font-weight:700;font-size:14px;color:var(--ink)}
.nav a{position:absolute;white-space:nowrap;color:inherit;text-decoration:none}
.nav .active{color:var(--green-bright)}

/* hero */
.hero{position:absolute;left:0;top:97px;width:1200px;height:680px;background:linear-gradient(180deg,#7e7fc4 0%,#a9a6db 30%,#d3d1ee 60%,#fff 100%)}
.hero-title{position:absolute;left:584px;top:356px;font-family:'Josefin Sans',sans-serif;font-weight:700;font-size:74px;color:var(--white);white-space:nowrap}
.scroll-down{position:absolute;left:578px;top:639px;width:44px;height:44px;border-radius:50%;background:var(--white);box-shadow:0 2px 6px rgba(0,0,0,.2)}

/* journey bar */
.journey{position:absolute;left:112px;top:785px;width:976px;height:90px;background:var(--white);box-shadow:0 4px 16px rgba(0,0,0,.08);border-left:4px solid var(--green)}
.journey-text{position:absolute;left:44px;top:26px;font-family:'Josefin Sans',sans-serif;font-weight:700;font-size:35px;color:var(--ink)}
.journey-btn{position:absolute;left:747px;top:27px;width:136px;height:38px;background:var(--white);color:var(--green);display:flex;align-items:center;justify-content:center;font-weight:700;font-size:14px}

/* about */
.about-title{left:112px;top:972px;font-size:46px}
.about-text{position:absolute;left:112px;width:464px;font-size:14.5px;line-height:21.5px;color:var(--body);text-align:justify}
.photo{position:absolute}

/* program */
.section-title{position:absolute;left:0;width:1200px;text-align:center;font-size:46px}
.program-label{position:absolute;top:1722px;font-weight:700;font-size:19px;color:var(--white);text-transform:uppercase;transform:translateX(-50%);white-space:nowrap}

/* team */
.member{position:absolute;top:2118px;width:240px;text-align:center;transform:translateX(-50%)}
.avatar{width:192px;height:192px;margin:0 auto;border-radius:50%;border:3px solid var(--green);padding:5px;background:var(--white)}
.avatar div{width:100%;height:100%;border-radius:50%}
.member-name{margin-top:16px;font-family:'Josefin Sans',sans-serif;font-weight:700;font-size:24px}
.member-role{margin-top:8px;font-size:14px;color:var(--body)}
.member-link{margin:16px auto 0;width:32px;height:32px;border-radius:50%;background:#eee;display:flex;align-items:center;justify-content:center}
.member-link span{width:10px;height:10px;background:#555;border-radius:2px}

/* tournament */
.tournament{position:absolute;left:0;top:2528px;width:1200px;height:685px;background:var(--field)}
.card-photo{position:absolute;top:168px;width:475px;height:391px}
.card-caption{position:absolute;top:360px;width:422px;height:56px;background:var(--white);display:flex;align-items:center;justify-content:space-between;padding:0 20px 0 27px;font-weight:700;font-size:21px;color:var(--ink)}
.go{width:28px;height:28px;border-radius:50%;background:var(--green-bright)}

/* footer */
.site-footer{position:absolute;left:0;top:3213px;width:1200px;height:387px;background:var(--footer);color:#ddd}
.footer-heading{position:absolute;top:112px;font-family:'Josefin Sans',sans-serif;font-weight:700;font-size:23px;color:var(--white)}
.footer-text{position:absolute;font-size:14px;line-height:26px;color:#ddd}
.footer-brand{position:absolute;left:460px;top:120px;width:280px;text-align:center;font-family:'Josefin Sans',sans-serif;font-weight:700;font-size:40px;line-height:44px;color:var(--white)}
.contact-row{position:absolute;left:788px;display:flex;gap:10px;font-size:14px;line-height:26px}
.contact-row svg{flex:none;margin-top:6px}
.copyright{position:absolute;left:0;top:3497px;width:1200px;text-align:center;font-size:14px;color:#ddd}
.socials{position:absolute;left:508px;top:3530px;display:flex;gap:6px}
.socials span{width:32px;height:32px;border:1px solid #888;border-radius:50%}
</style>
</head>
<body>

<header class="site-header">
  <div class="brand">Bramble Hockey</div>
  <nav class="nav">
    <a class="active" style="left:506px">Home</a>
    <a style="left:580px">About</a>
    <a style="left:656px">Program &#8964;</a>
    <a style="left:762px">Team</a>
    <a style="left:833px">Tournament</a>
  </nav>
  <div class="btn" style="left:953px;top:35px;width:135px;height:40px">Get a Quote</div>
</header>

<section class="hero" role="img" aria-label="Ice hockey player skating hard with ice spray under purple arena lights">
</section>
<div class="hero-title">Bramble Hockey</div>
<div class="btn" style="left:585px;top:440px;width:135px;height:38px">Get Started</div>
<div class="scroll-down">
  <svg width="44" height="44" viewBox="0 0 44 44"><path d="M22 13v17M15 24l7 7 7-7" fill="none" stroke="#222" stroke-width="2.4" stroke-linecap="round" stroke-linejoin="round"/></svg>
</div>

<div class="journey">
  <svg class="abs" style="left:596px;top:0" width="376" height="90" viewBox="0 0 376 90"><polygon points="76,0 376,0 376,90 0,90" fill="var(--green-dark)"/></svg>
  <div class="journey-text">Get Ready to Start Your Journey</div>
  <div class="journey-btn">GAME ON</div>
</div>

<h2 class="heading abs about-title">About Us</h2>
<p class="about-text" style="top:1038px">Lorem ipsum dolor sit amet, consectetur adipiscing elit, sed do eiusmod tempor incididunt ut labore et dolore magna aliqua. Ut enim ad minim veniam, quis nostrud exercitation ullamco laboris nisi ut aliquip ex ea commodo consequat. Duis aute irure dolor in reprehenderit in voluptate velit esse cillum dolore eu fugiat nulla pariatur.</p>
<p class="about-text" style="top:1167px">Excepteur sint occaecat cupidatat non proident, sunt in culpa qui officia deserunt mollit anim id est laborum. Lorem ipsum dolor sit amet, consectetur adipiscing elit, sed do eiusmod tempor incididunt ut labore et dolore magna aliqua. Ut enim ad minim veniam, quis nostrud exercitation ullamco laboris nisi ut aliquip ex ea commodo consequat. Duis aute irure dolor in reprehenderit</p>
<div class="btn" style="left:112px;top:1316px;width:134px;height:39px">Read More &#10230;</div>
<svg class="abs" style="left:625px;top:975px" width="495" height="385" viewBox="0 0 495 385">
  <polygon points="80,3 115,3 35,108 0,108" fill="var(--green)" transform="translate(3,0)"/>
  <polygon points="450,278 490,278 400,385 360,385" fill="var(--green)"/>
</svg>
<div class="photo" role="img" aria-label="Ice hockey players colliding on the rink under bright arena lights" style="left:652px;top:978px;width:436px;height:377px;background:linear-gradient(160deg,#3e68a8,#8fb0d8 55%,#dfe7f0)"></div>
<svg class="abs" style="left:625px;top:975px" width="495" height="385" viewBox="0 0 495 385">
  <polygon points="83,3 110,3 27,100 27,70" fill="var(--green)"/>
  <polygon points="463,278 490,278 410,385 380,385" fill="var(--green)"/>
</svg>

<h2 class="heading section-title" style="top:1452px">Our Program</h2>
<svg class="abs" style="left:0;top:1531px" width="1200" height="405" viewBox="0 0 1200 405" role="img" aria-label="Program photos: winter ice hockey, spring hockey with green overlay, summer field hockey">
  <polygon points="8,0 426,0 376,405 8,405" fill="#4a4f5c"/>
  <polygon points="441,0 759,0 808,405 393,405" fill="#2f9a2f"/>
  <polygon points="775,0 1192,0 1192,405 824,405" fill="#7c7a63"/>
</svg>
<div class="program-label" style="left:218px">Winter Program</div>
<div class="program-label" style="left:601px">Spring Program</div>
<div class="program-label" style="left:983px">Summer Program</div>

<h2 class="heading section-title" style="top:2033px">Our Team</h2>
<div class="member" style="left:235px">
  <div class="avatar"><div role="img" aria-label="Team member portrait" style="background:#dcdcdc"></div></div>
  <div class="member-name">JOHN DOE</div><div class="member-role">Company name</div><div class="member-link"><span></span></div>
</div>
<div class="member" style="left:479px">
  <div class="avatar"><div role="img" aria-label="Team member portrait" style="background:#e3b774"></div></div>
  <div class="member-name">JOHN DOE</div><div class="member-role">Company name</div><div class="member-link"><span></span></div>
</div>
<div class="member" style="left:724px">
  <div class="avatar"><div role="img" aria-label="Team member portrait" style="background:#e4e4e4"></div></div>
  <div class="member-name">JOHN DOE</div><div class="member-role">Company name</div><div class="member-link"><span></span></div>
</div>
<div class="member" style="left:967px">
  <div class="avatar"><div role="img" aria-label="Team member portrait" style="background:#e8e8e8"></div></div>
  <div class="member-name">JOHN DOE</div><div class="member-role">Company name</div><div class="member-link"><span></span></div>
</div>

<section class="tournament">
  <h2 class="heading section-title" style="top:96px;color:var(--white)">Tournament</h2>
  <svg class="abs" style="left:48px;top:355px" width="24" height="36" viewBox="0 0 24 36"><path d="M18 4L6 18l12 14" fill="none" stroke="#fff" stroke-width="3.5"/></svg>
  <svg class="abs" style="left:1130px;top:355px" width="24" height="36" viewBox="0 0 24 36"><path d="M6 4l12 14L6 32" fill="none" stroke="#fff" stroke-width="3.5"/></svg>
  <div class="card-photo" role="img" aria-label="Field hockey player driving the ball on a red court" style="left:112px;background:linear-gradient(160deg,#5a3c33,#b06a52 50%,#c9876b)"></div>
  <div class="card-photo" role="img" aria-label="Ice hockey player skating under arena spotlights" style="left:614px;background:radial-gradient(circle at 35% 45%,#dfe6f5,#3d5488 40%,#131e3c)"></div>
  <div class="card-caption" style="left:138px">Lorem ipsum dolor sit amet<span class="go"></span></div>
  <div class="card-caption" style="left:640px">Lorem ipsum dolor sit amet<span class="go"></span></div>
</section>

<footer class="site-footer">
  <div class="footer-heading" style="right:781px">ABOUT US</div>
  <p class="footer-text" style="left:112px;top:146px;width:307px;text-align:right">Lorem ipsum dolor sit amet, consectetur adip iscing elit, sed do eiusmod tempor incidi dunt ut labore et dolore magna aliqua. Ut enim ad minim veniam, quis nostrud</p>
  <div class="footer-brand">Bramble<br>Hockey</div>
  <div class="footer-heading" style="left:788px">CONTACT US</div>
  <div class="contact-row" style="top:146px;width:320px">
    <svg width="10" height="14" viewBox="0 0 10 14"><path d="M5 0a5 5 0 0 0-5 5c0 4 5 9 5 9s5-5 5-9a5 5 0 0 0-5-5z" fill="var(--green-bright)"/><circle cx="5" cy="5" r="2" fill="var(--footer)"/></svg>
    <span>Lorem ipsum dolor sit amet, consectetur adip iscing elit, sed do eiusmod</span>
  </div>
  <div class="contact-row" style="top:198px">
    <svg width="12" height="12" viewBox="0 0 12 12"><path d="M2 0l3 3-1.5 2a7 7 0 0 0 3.5 3.5L9 7l3 3-2 2C5 12 0 7 0 2z" fill="var(--green-bright)"/></svg>
    <span>+1 888 888 8888</span>
  </div>
  <div class="contact-row" style="top:224px">
    <svg width="12" height="10" viewBox="0 0 12 10"><rect width="12" height="10" rx="1" fill="var(--green-bright)"/><path d="M0 1l6 4 6-4" fill="none" stroke="var(--footer)" stroke-width="1.2"/></svg>
    <span>info@companyname.com</span>
  </div>
</footer>
<div class="copyright">&copy; Copyrights 2023 Company Name | All Rights reserved</div>
<div class="socials"><span></span><span></span><span></span><span></span><span></span></div>

</body>
</html>
```